PowerPoint Design for KESTREL Polls

KESTREL Polls stands for 'Kindred Evaluation Scales Tracking Regional Electoral Leanings'. It is a collaborative research effort to format and combine multiple sources of public opinion data from around the world into merged datasets. We need a Microsoft PowerPoint design for our conference/workshop presentations and instructional videos used as part of our research efforts and crowdsourced development. The design should match the website design and logo, which are attached to this contest (these are the files from previous successful design contests).

Slides will contain a lot of data visualizations, tables with statistical output (lots of numbers), and figures. Bullet points will be used frequently on slides and larg blocks of text should be avided. Margins should be narrow to maximize space used and the size of fonts must be large enough (24-32+) to be visible at the back of classrooms and conference rooms.
Updates

I was away at a conference and am now busy with teaching preparation, so I need a few extra days to give adequate feedback.

Target Market(s)

academia, government, non-profits, postgraduates, researchers

Font styles to use
Sans Serif

Colors

Designer to choose colors to be used in the design.

Requirements
Must have
• designs for common slide layouts
Nice to have
• thematic link with website design and logo

```html
<!DOCTYPE html>
<html lang="en">
<head>
<meta charset="UTF-8">
<title>KESTREL Polls – Slide Template</title>
<link href="https://fonts.googleapis.com/css2?family=Open+Sans:wght@400;600;700&display=swap" rel="stylesheet">
<style>
  :root {
    --brand-blue: #1676c0;
    --brand-blue-dark: #0f66ad;
    --accent-blue: #29a3e3;
    --bullet-blue: #2a9ad8;
    --text-dark: #3a3a3a;
    --footer-grey: #9d9d9d;
    --white: #ffffff;
  }
  * { box-sizing: border-box; margin: 0; padding: 0; }
  html, body { width: 1200px; height: 900px; overflow: hidden; background: var(--white); }
  body { font-family: "Open Sans", Arial, sans-serif; color: var(--text-dark); }

  .slide { position: relative; width: 1200px; height: 900px; background: var(--white); overflow: hidden; }

  .slide-header {
    position: absolute; left: 0; top: 0; width: 1200px; height: 66px;
    background: linear-gradient(90deg, var(--brand-blue-dark), var(--brand-blue));
    display: flex; align-items: center; padding-left: 18px;
  }
  .slide-title { color: var(--white); font-weight: 700; font-size: 33px; letter-spacing: 0.5px; }
  .header-rule { position: absolute; left: 0; top: 68px; width: 1080px; height: 6px; background: var(--accent-blue); }

  .brand-name {
    position: absolute; right: 22px; top: 0; height: 66px;
    display: flex; align-items: center; gap: 10px;
    color: var(--white); font-weight: 700; font-size: 22px;
  }
  .brand-name .brand-dot { width: 14px; height: 14px; border-radius: 50%; background: var(--white); }

  .bullet-list { position: absolute; left: 30px; top: 134px; width: 1100px; list-style: none; }
  .bullet { position: relative; padding-left: 65px; font-size: 22px; line-height: 33px; margin-bottom: 34px; }
  .bullet::before {
    content: ""; position: absolute; left: 11px; top: 6px; width: 22px; height: 22px;
    border: 3px solid var(--bullet-blue); border-radius: 50%;
  }
  .sub-list { list-style: none; margin-top: 24px; margin-left: 75px; }
  .sub-bullet { position: relative; padding-left: 40px; font-size: 20px; line-height: 30px; margin-bottom: 34px; }
  .sub-bullet.dot::before {
    content: ""; position: absolute; left: 0; top: 6px; width: 18px; height: 18px;
    background: var(--bullet-blue); border-radius: 50%;
  }
  .sub-bullet .tick { position: absolute; left: -2px; top: 6px; width: 24px; height: 22px; }

  .slide-footer {
    position: absolute; left: 0; bottom: 0; width: 1200px; height: 45px;
    background: var(--footer-grey); display: flex; align-items: center; padding-left: 12px;
  }
  .copyright { color: var(--white); font-weight: 700; font-size: 19px; }
  .page-number { position: absolute; right: 0; bottom: 0; width: 110px; height: 45px; }
  .page-number span {
    position: absolute; right: 28px; top: 0; line-height: 45px;
    color: var(--white); font-weight: 700; font-size: 20px;
  }
</style>
</head>
<body>
<div class="slide">
  <header class="slide-header">
    <h1 class="slide-title">PROJECT TITLE HERE</h1>
    <div class="brand-name"><span class="brand-dot"></span>KESTREL Polls</div>
  </header>
  <div class="header-rule"></div>

  <ul class="bullet-list">
    <li class="bullet">This page has more than four top-level bullets, so the second-level bullet format is used (just indent the first bullet)</li>
    <li class="bullet">Second level bullet (18 pt Verdana)</li>
    <li class="bullet">Second and subsequent level bullets use a “dot” bullet</li>
    <li class="bullet">The bullet color is Red 232; Green 95; Blue 49</li>
    <li class="bullet">Spacing and font sizing may be manually adjusted if necessary</li>
    <li class="bullet">Try first to edit the text to allow it to fit without changing spacing or size (3rd level = 16 pt)
      <ul class="sub-list">
        <li class="sub-bullet dot">This fosters readability and a consistent look (4th level = 14 pt)</li>
        <li class="sub-bullet">
          <svg class="tick" viewBox="0 0 24 22" aria-hidden="true"><path d="M2 12 L9 19 L22 3" fill="none" stroke="#2a9ad8" stroke-width="4" stroke-linecap="round" stroke-linejoin="round"/></svg>
          Sometimes there is just too much to say and you will have to adjust
        </li>
      </ul>
    </li>
  </ul>

  <footer class="slide-footer">
    <span class="copyright">Copyright text here</span>
    <div class="page-number">
      <svg width="110" height="45" viewBox="0 0 110 45" aria-hidden="true">
        <path d="M14 0 H110 V45 H14 L4 22.5 Z" fill="#ffffff"/>
        <path d="M20 4 H110 V45 H20 L11 24 Z" fill="#29a3e3"/>
      </svg>
      <span>01</span>
    </div>
  </footer>
</div>
</body>
</html>
```